Private Investment Firm Needs PowerPoint Presentation Template

Design PowerPoint template, take Pinebrook-submitted rough presentation draft, and drop it into new template. See attached Project Brief file for more detail.
Updates

Some decent designs have been submitted but they seem to lack the understanding of our target markets. I am hopeful that more time and feedback will result in better results.

Target Market(s)

Private company owners and intermediaries.

Font styles to use
Serif

Colors
3176b5

Requirements
Must have
• See attached Project Brief.
Nice to have
Should not have
• No B2C fluff--this is a B2B project.

```html
<!DOCTYPE html>
<html lang="en">
<head>
<meta charset="utf-8">
<title>Pinebrook Representative Non-Control Capital Investments</title>
<link href="https://fonts.googleapis.com/css2?family=Montserrat:wght@400;500;600;700&family=Libre+Baskerville:wght@400;700&display=swap" rel="stylesheet">
<style>
  :root {
    --brand-blue: #3176b5;
    --title-blue: #1e6fc2;
    --bar-blue: #1a6fc4;
    --ink: #2b2b2b;
    --navy: #1d3a63;
    --card-border: #dfe5ec;
    --white: #ffffff;
  }
  * { box-sizing: border-box; margin: 0; padding: 0; }
  html, body { width: 1200px; height: 676px; overflow: hidden; background: var(--white); }
  .slide {
    position: relative; width: 1200px; height: 676px; overflow: hidden;
    background: var(--white); font-family: "Montserrat", Arial, sans-serif; color: var(--ink);
  }
  .side-bar { position: absolute; left: 0; top: 0; width: 44px; height: 676px; background: var(--bar-blue); }
  .edge-bar { position: absolute; right: 0; top: 0; width: 12px; height: 676px; background: var(--bar-blue); }
  .site-url {
    position: absolute; left: 22px; top: 336px;
    transform: translate(-50%, -50%) rotate(-90deg);
    font-family: "Libre Baskerville", Georgia, serif; font-size: 14px; color: var(--white);
    white-space: nowrap; letter-spacing: 0.3px;
  }
  .page-number {
    position: absolute; right: 22px; top: 18px;
    font-family: "Libre Baskerville", Georgia, serif; font-size: 17px; color: var(--ink);
  }
  .slide-title {
    position: absolute; left: 86px; top: 80px;
    font-size: 29px; font-weight: 700; color: var(--title-blue); letter-spacing: 0.2px;
  }
  .investments { position: absolute; left: 86px; top: 138px; width: 1080px; }
  .investment { position: relative; height: 66px; margin-bottom: 8.5px; }
  .investment-card {
    position: absolute; left: 0; top: 0; width: 922px; height: 66px;
    border: 1px solid var(--card-border); border-radius: 8px 34px 34px 8px;
    box-shadow: 0 1px 3px rgba(0,0,0,0.08); padding: 5px 18px 0 11px;
  }
  .investment-type { font-size: 12px; font-weight: 600; color: var(--title-blue); margin-bottom: 3px; }
  .investment-points { list-style: none; }
  .investment-points li {
    position: relative; padding-left: 18px; font-size: 7.4px; line-height: 8.6px;
    font-weight: 500; margin-bottom: 3px;
  }
  .investment-points li::before {
    content: ""; position: absolute; left: 2px; top: 1.5px; width: 4px; height: 4px;
    border: 1.5px solid var(--title-blue); transform: rotate(45deg);
  }
  .company-mark {
    position: absolute; left: 940px; top: 0; width: 140px; height: 66px;
    display: flex; align-items: center; gap: 6px;
    font-family: "Montserrat", Arial, sans-serif; font-size: 13px; font-weight: 700; color: var(--navy);
    line-height: 1.1;
  }
  .company-mark .mark-square { flex: 0 0 12px; height: 12px; background: var(--navy); }
  .firm-signature { position: absolute; left: 68px; top: 612px; }
  .firm-name {
    font-family: "Libre Baskerville", Georgia, serif; font-size: 17px; font-weight: 400;
    color: var(--navy); letter-spacing: 1.5px;
  }
  .firm-tagline {
    margin-top: 4px; padding-top: 3px; border-top: 1px solid var(--brand-blue);
    font-family: "Libre Baskerville", Georgia, serif; font-size: 6px; color: var(--brand-blue);
    letter-spacing: 0.6px; text-transform: uppercase;
  }
</style>
</head>
<body>
<div class="slide">
  <div class="side-bar"></div>
  <div class="edge-bar"></div>
  <div class="site-url">www.pinebrookcapital.com</div>
  <div class="page-number">11</div>

  <h1 class="slide-title">PINEBROOK REPRESENTATIVE NON-CONTROL CAPITAL INVESTMENTS</h1>

  <div class="investments">
    <section class="investment">
      <div class="investment-card">
        <h2 class="investment-type">Growth Capital</h2>
        <ul class="investment-points">
          <li>Operates dedicated commercial airline pilot training facilities throughout the U.S. and Mexico. Centers are complete with classrooms; integrated procedures trainers; flight training devices; and Level D, full-motion flight simulators.</li>
          <li>Pinebrook’s capital was used to fund the Company’s near to intermediate-term growth. Pinebrook also assisted the Company in the recruitment of additional management personnel and the opening of a new Dallas office.</li>
        </ul>
      </div>
      <div class="company-mark"><span class="mark-square"></span>Skyward Flight Group</div>
    </section>

    <section class="investment">
      <div class="investment-card">
        <h2 class="investment-type">Management Buy-Out (MBO)</h2>
        <ul class="investment-points">
          <li>Provider of audit compliance software and consulting services for hospitals and physician practices.</li>
          <li>Pinebrook’s capital was used to assist the active CEO in acquiring the business from its inactive founder. Pinebrook also assisted in the significant investment into the Company’s core revenue integrity software platform, developing it into the premier risk-based product in its sector.</li>
        </ul>
      </div>
      <div class="company-mark"><span class="mark-square"></span>Halden Compliance</div>
    </section>

    <section class="investment">
      <div class="investment-card">
        <h2 class="investment-type">Acquisition Finance</h2>
        <ul class="investment-points">
          <li>Manufacturer of vibration isolation, seismic control, and shock protection products. The Company’s products are designed to limit the transmission of vibration, impact, seismic, and wind forces to protect larger systems that are at risk of damage from these events.</li>
          <li>Pinebrook’s capital was used to acquire two attractive tuck-in companies (a testing lab and an on-line component distributor) that improved Verity’s competitive position. Three years later, the Company set an all-time sales record.</li>
        </ul>
      </div>
      <div class="company-mark"><span class="mark-square"></span>Verity Mounts Group</div>
    </section>

    <section class="investment">
      <div class="investment-card">
        <h2 class="investment-type">Balance Sheet Recapitalization</h2>
        <ul class="investment-points">
          <li>Provider of third-party vehicle maintenance services for private, public, and for-hire fleet-based businesses nationwide.</li>
          <li>Pinebrook’s capital was used to support Fleetwise’s accelerating growth which exceeded their current lender’s capacity. Pinebrook provided both subordinated debt and preferred stock, altered the debt and equity mix of the business, and the Company was able to grow significantly over the next three years.</li>
        </ul>
      </div>
      <div class="company-mark"><span class="mark-square"></span>Fleetwise Services</div>
    </section>

    <section class="investment">
      <div class="investment-card">
        <h2 class="investment-type">Family Ownership &amp; Wealth</h2>
        <ul class="investment-points">
          <li>Provider of fire and security alarm design, installation, service, and monitoring services for commercial and residential end-markets.</li>
          <li>Pinebrook’s capital allowed for enough cash breathing room for the CEO to think strategically about the business, focus on the growth of the Company, and build family wealth. Five years later, after the Company and Pinebrook were successful in substantially growing the business, Ridgeline Alarm bought out Pinebrook’s ownership position entirely with senior debt—as a result, the CEO (father), COO (son), and key management team were back to owning 100% of the Company. The son had a significantly larger stake in the business than five years earlier and the father had the flexibility to work through his family estate plans.</li>
        </ul>
      </div>
      <div class="company-mark"><span class="mark-square"></span>Ridgeline Alarm</div>
    </section>

    <section class="investment">
      <div class="investment-card">
        <h2 class="investment-type">Family Office Support</h2>
        <ul class="investment-points">
          <li>Provides comprehensive and custom packaging for the liquid home cleaning products sector, and has the ability to safely process volatile liquids, such as bleach and hydrogen peroxide.</li>
          <li>Pinebrook’s capital was used to assist a New York-based family office in acquiring the Company as part of their business outsourcing growth strategy thesis.</li>
        </ul>
      </div>
      <div class="company-mark"><span class="mark-square"></span>Corvo Packaging</div>
    </section>
  </div>

  <div class="firm-signature">
    <div class="firm-name">PINEBROOK CAPITAL</div>
    <div class="firm-tagline">Non-Control Growth Capital</div>
  </div>
</div>
</body>
</html>
```